Web Design for Webdesign company 3 page PSD

Project
---------
We need a PSD Web Design to be used in a WordPress installation.
What we would like to create is a professional looking website for a web design agency. We also need you to look for suitable stock images to be placed on these pages.
We need the design for:
Homepage
Landing page
Contact page
attached in the pages file you will find a file with more in depth details how these files should be build up.
We would like to see a desktop version and a mobile version of these pages
The website should have a 1100px width.
The mobile design should have 480px width.
The homepage should have a header slider about 450px high.
The slider is preferred full width and should have some images text and a button
Objectives
-------------
The main objective for the website is to get leads from customers in the form of a request for a quotation or a call or mail me back action. The most important action for the homepage is to link and navigate to our landing pages.
What we want to tell our visitors (our main products)
-------------------------------------------------------------------
- A website with no big investment but a monthly rate
- A successful website with no worries (a complete website, seo, hosting and a service contract for future customization is included for a monthly rate)
Color Scheme
------------
Use branding colors. You can find them in the branding.pdf file.
Additional colors:
White: #ffffff
Black: #181818
Company info
--------------
We are a starting web design / marketing agency based in The Netherlands and looking for the design of our website. Our services are (custom) webdesign, website marketing or combinations of both. Our main customer group is small business owners.
We sell websites but give the option to buy it with a lease contract.
A second product is a default website with a complete service: SEO, hosting and a service contract for a monthly rate.
Content:
-----------
If not available place Lorem Ipsum text.
There will come about 400 words of text on the landing pages
Design Competition
--------------------------
Since this is a designing competition we would like to see your creativity.
What you can expect from us is a lot of feedback 7 days a week with short response time.
You can send us the first sketchy mock ups of the homepage and we will give feedback based on these design. But we like your feedback or comments as well
Read the pages file for more in depth details how the pages should be designed

Target Market(s)
Small business owners in The Netherlands
Industry/Entity Type
It Company
Number of Pages Required
3 page
Requirements
Must have
- Homepage:
- Header slider with images, some text and a link to a custom page
- The slider should have 3 designed slides
- Landings page:
- Sidebar
- Action button for a request for a quotation
- Action button for a call me back action
- Action button for an appointment
- Contact form:
- Address details
- Contact form
Nice to have
- Homepage:
- Full width slider
- Testimonial block
- Blog items
Should not have
- Flash
- A to crowded design

```html
<!DOCTYPE html>
<html lang="en">
<head>
<meta charset="utf-8">
<title>Willow Lane Web Studio</title>
<link rel="stylesheet" href="https://fonts.googleapis.com/css2?family=Ubuntu:wght@400;500;700&family=Open+Sans:wght@400;600&display=swap">
<style>
:root{
  --teal:#3d8280;
  --teal-box:rgba(61,128,128,.88);
  --green:#22b07d;
  --green-light:#6fc17c;
  --ink:#181818;
  --text:#444;
  --white:#ffffff;
  --footer-bg:#f4f4f4;
  --bar-bg:#232323;
}
*{margin:0;padding:0;box-sizing:border-box}
html,body{width:1200px;height:985px;overflow:hidden}
body{position:relative;font-family:"Open Sans",sans-serif;color:var(--text);background:var(--white)}

.site-header{position:absolute;left:0;top:0;width:1200px;height:115px;background:#fbfbfb;border-top:1px solid #e6e6e6}
.brand{position:absolute;left:100px;top:31px;display:flex;align-items:center;gap:12px}
.brand-mark{width:50px;height:50px;border-radius:50%;background:var(--teal)}
.brand-name{font-family:"Open Sans",sans-serif;font-weight:600;font-size:17px;color:var(--teal);white-space:nowrap}
.main-nav{position:absolute;top:0;left:637px;display:flex;height:115px}
.main-nav a{position:relative;font-family:"Open Sans",sans-serif;font-size:12.5px;color:#333;text-decoration:none;line-height:121px;margin-right:46px;white-space:nowrap}
.main-nav a:last-child{margin-right:0}
.main-nav a.is-active::before{content:"";position:absolute;left:-9px;right:-13px;top:0;height:3px;background:var(--teal)}

.hero{position:absolute;left:0;top:115px;width:1200px;height:482px;background:linear-gradient(120deg,#23ae80 0%,#4fba7a 35%,#86c16f 55%,#5fbd79 70%,#22ad80 100%)}
.hero-visual{position:absolute;left:118px;top:68px;width:352px;height:335px;border-radius:10px;background:linear-gradient(160deg,#cfe3ec,#8fb0c0 60%,#c8c8c8)}
.hero-copy{position:absolute;left:628px;top:132px;color:var(--white)}
.hero-title{font-family:"Ubuntu",sans-serif;font-weight:700;font-size:51px;line-height:54px;letter-spacing:.5px}
.hero-price{font-family:"Ubuntu",sans-serif;font-weight:400;font-size:39px;line-height:44px}
.hero-text{margin-top:22px;margin-left:4px;font-size:16px;line-height:23px}
.hero-button{display:inline-flex;align-items:center;gap:6px;margin:24px 0 0 6px;height:45px;padding:0 22px;background:var(--white);border-radius:3px;color:var(--teal);font-size:16px;text-decoration:none}

.action-band{position:absolute;left:0;top:597px;width:1200px;height:97px;background:linear-gradient(90deg,#9a7a5c,#c8b49e 30%,#a78a6d 60%,#cbb9a4)}
.action{position:absolute;top:0;width:317px;height:97px;background:var(--teal-box);text-align:center}
.action-icon{position:absolute;left:118px;top:-40px;width:80px;height:80px;border-radius:50%;background:var(--teal);border:4px solid #d8e4e3;display:flex;align-items:center;justify-content:center}
.action-label{position:absolute;left:0;right:0;top:52px;font-size:19px;color:var(--white);font-family:"Open Sans",sans-serif}

.info{position:absolute;left:0;top:694px;width:1200px;height:232px;background:var(--footer-bg)}
.info h3{font-family:"Open Sans",sans-serif;font-weight:400;font-size:15px;color:#333;margin-bottom:14px}
.about{position:absolute;left:98px;top:42px;width:380px}
.about p{font-size:11.3px;line-height:20.5px;color:#444}
.social{display:flex;gap:9px;margin-top:14px}
.social span{width:29px;height:29px;display:block}
.newsletter{position:absolute;left:562px;top:42px;width:264px}
.newsletter p{font-size:11.3px;line-height:19px;text-align:justify}
.signup{display:flex;margin-top:15px;height:41px}
.signup-field{width:165px;background:var(--white);border:1px solid #e3e3e3;font-size:11.5px;color:#444;padding:0 13px;line-height:39px}
.signup-button{width:97px;background:var(--green-light);color:var(--white);font-size:13px;line-height:41px;text-align:center}
.contact{position:absolute;left:930px;top:42px;width:240px;font-size:12.5px;color:#333}
.contact p{line-height:20px}
.contact-row{display:flex;align-items:center;gap:14px;margin-top:6px;height:20px}
.contact-row:first-of-type{margin-top:13px}

.legal{position:absolute;left:0;top:926px;width:1200px;height:59px;background:var(--bar-bg);text-align:center;font-size:11.5px;line-height:59px;color:#bbb}
.legal strong{font-weight:400;color:var(--green-light)}
</style>
</head>
<body>
<header class="site-header">
  <div class="brand">
    <span class="brand-mark"></span>
    <span class="brand-name">Willow Lane Web Studio</span>
  </div>
  <nav class="main-nav">
    <a href="#" class="is-active">HOME</a>
    <a href="#">ABOUT US</a>
    <a href="#">OUR SERVICES</a>
    <a href="#">NEWS</a>
    <a href="#">CONTACT US</a>
  </nav>
</header>

<section class="hero">
  <div class="hero-visual" role="img" aria-label="Desktop computer displaying website layouts"></div>
  <div class="hero-copy">
    <h1 class="hero-title">A WEBSITE FROM</h1>
    <p class="hero-price">€19,95 per month</p>
    <p class="hero-text">With us, you can lease a website. So no big investment upfront.<br>A website is available from € 19.95 per month</p>
    <a class="hero-button" href="#">MORE INFORMATION
      <svg width="13" height="13" viewBox="0 0 14 14"><circle cx="7" cy="7" r="7" fill="#3d8280"/><path d="M5.5 4 8.5 7 5.5 10" stroke="#fff" stroke-width="2" fill="none"/></svg>
    </a>
  </div>
</section>

<section class="action-band" role="img" aria-label="Wooden floor boards background">
  <div class="action" style="left:99px">
    <div class="action-icon">
      <svg width="36" height="28" viewBox="0 0 36 28" fill="#fff"><path d="M2 10c0-6 32-6 32 0v3h-8v-4c-4-2-12-2-16 0v4H2z"/><rect x="6" y="15" width="24" height="11" rx="2"/></svg>
    </div>
    <div class="action-label">CALL ME BACK</div>
  </div>
  <div class="action" style="left:441px">
    <div class="action-icon">
      <svg width="32" height="24" viewBox="0 0 32 24" fill="none" stroke="#fff" stroke-width="3"><rect x="2" y="2" width="28" height="20" rx="3"/><path d="M3 4 16 14 29 4"/></svg>
    </div>
    <div class="action-label">MAKE AN APPOINTMENT</div>
  </div>
  <div class="action" style="left:784px">
    <div class="action-icon">
      <svg width="36" height="30" viewBox="0 0 36 30" fill="none" stroke="#fff" stroke-width="3"><ellipse cx="14" cy="12" rx="12" ry="9"/><path d="M6 19 4 26 12 21"/><path d="M24 8c6 1 10 5 9 9-1 3-3 5-6 6l2 5-7-4"/></svg>
    </div>
    <div class="action-label">REQUEST A QUOTATION</div>
  </div>
</section>

<section class="info">
  <div class="about">
    <h3>ABOUT OUR COMPANY</h3>
    <p>rem ipsum dolor sit amet, consectetur adipisicing elit. Minima, minus iure accusantium dolores, officiis eveniet architecto error placeat ratione incidunt? rem ipsum dolor sit amet, consectetur adipisicing elit. Minima, minus iure accusantium dolores,</p>
    <div class="social">
      <span style="background:#dd4b39" aria-label="Social network"></span>
      <span style="background:#3b5998" aria-label="Social network"></span>
      <span style="background:#1da1f2" aria-label="Social network"></span>
      <span style="background:#0e76a8" aria-label="Social network"></span>
      <span style="background:#d9352a" aria-label="Social network"></span>
    </div>
  </div>
  <div class="newsletter">
    <h3>SIGN UP FOR NEWSLETTER</h3>
    <p>Excepteur sint occaecat cupidatat non proident, sunt in culpa qui officia deserunt</p>
    <div class="signup">
      <div class="signup-field">Enter Name</div>
      <div class="signup-button">SUBSCRIBE</div>
    </div>
  </div>
  <div class="contact">
    <h3>CONTACT US</h3>
    <p>Willow Lane<br>PO BOX 12, Riverton</p>
    <div class="contact-row">
      <svg width="19" height="19" viewBox="0 0 20 20" fill="none" stroke="#6fc17c" stroke-width="1.4"><path d="M4 2l3 3-2 3c1 3 4 6 7 7l3-2 3 3-3 3C8 18 2 12 1 5z"/></svg>
      <span>+1 5550 123 456</span>
    </div>
    <div class="contact-row">
      <svg width="19" height="14" viewBox="0 0 20 14" fill="none" stroke="#6fc17c" stroke-width="1.4"><rect x="1" y="1" width="18" height="12"/><path d="M1 1l9 7 9-7M1 13l6-6M19 13l-6-6"/></svg>
      <span>hello@willowlane.example</span>
    </div>
  </div>
</section>

<footer class="legal">©2014 - 2015 &nbsp;<strong>WILLOW LANE.</strong>. All Rights Reserved.</footer>
</body>
</html>
```